Vorn upkeep KT Solar Venture

Solar power system install
Services and maintenance
wiring, Rewinding and Renovation
Switch Board Upgrade
Power and lighting point
t doesn’t matter how much you spend on quality parts, your solar system will let you down if your design and installation are sub-par. Have your solar system tailored and installed by our Master Electrician and Bright Grid Guild Accredited team.

Target Market(s)

sales and installed

Industry/Entity Type

Solar install and retailer

Contact Information for Business Card

Name , Email, Phone Number ,Business address,

Font styles to use
Serif

Colors
0054AA
0677BA
7BADD7
CADEEF
E8F1F8

Requirements
Must have
• clear and bright
Nice to have
• new design
Should not have
• unclear pictures

```html
<!DOCTYPE html>
<html lang="en">
<head>
<meta charset="utf-8">
<title>Vorn Upkeep – Business Card</title>
<link href="https://fonts.googleapis.com/css2?family=Roboto:wght@400;500;700;900&display=swap" rel="stylesheet">
<style>
  :root{
    --bg:#2d2d2d;
    --blue-deep:#0054AA;
    --blue:#0677BA;
    --blue-soft:#7BADD7;
    --blue-pale:#CADEEF;
    --blue-mist:#E8F1F8;
    --green:#2e9a3a;
    --green-light:#7cc242;
    --ink:#1d1d1d;
    --white:#ffffff;
    --paper:#efefef;
  }
  *{margin:0;padding:0;box-sizing:border-box}
  html,body{width:1200px;height:1138px;overflow:hidden;background:var(--bg);font-family:"Roboto",sans-serif}
  .canvas{position:relative;width:1200px;height:1138px}
  .card{position:absolute;width:620px;height:376px;border-radius:16px;overflow:hidden}
  .card svg.shape{position:absolute;inset:0}
  .card--front{left:274px;top:185px}
  .card--back{left:276px;top:608px;background:linear-gradient(180deg,#f6f6f6,var(--paper))}

  .brand{position:absolute;display:flex;align-items:center;gap:12px}
  .brand__dot{width:64px;height:64px;border-radius:50%;flex:none}
  .brand__name{font-weight:900;letter-spacing:.5px;line-height:1}
  .card--front .brand{left:300px;top:58px}
  .card--front .brand__dot{background:var(--blue-pale)}
  .card--front .brand__name{color:var(--white);font-size:28px}

  .services{position:absolute;right:28px;top:230px;list-style:none;text-align:right;color:var(--white);font-size:16px;line-height:22.4px}
  .services li::after{content:"«";margin-left:10px}

  .card--back .brand{left:40px;top:60px;flex-direction:column;gap:18px;width:236px}
  .card--back .brand__dot{width:120px;height:120px;background:var(--blue-pale);border:6px solid var(--blue)}
  .card--back .brand__name{color:var(--blue-deep);font-size:30px}

  .contact{position:absolute;left:343px;top:72px;color:var(--ink)}
  .contact__name{color:var(--blue);font-size:25px;font-weight:700}
  .contact__role{font-size:16px;margin-top:4px}
  .contact__address{font-size:16px;line-height:24px;margin-top:24px}
  .contact__list{list-style:none;margin-top:8px;font-size:16px;line-height:24px}
  .contact__list li{display:flex;align-items:center;gap:18px}
  .contact__list svg{width:14px;height:14px;flex:none;margin-left:2px}
  .tagline{position:absolute;left:343px;top:338px;color:var(--white);font-size:16px}
</style>
</head>
<body>
<main class="canvas">

  <section class="card card--front" aria-label="Card front">
    <svg class="shape" width="620" height="376" viewBox="0 0 620 376">
      <defs>
        <linearGradient id="frontBlue" x1="0" y1="0" x2="0.3" y2="1">
          <stop offset="0" stop-color="#0a4f9e"/>
          <stop offset="1" stop-color="#0a7fcd"/>
        </linearGradient>
        <linearGradient id="panelTone" x1="0.9" y1="0" x2="0.1" y2="1">
          <stop offset="0" stop-color="#c58a63"/>
          <stop offset="0.3" stop-color="#5a5f78"/>
          <stop offset="1" stop-color="#1f2436"/>
        </linearGradient>
      </defs>
      <rect width="620" height="376" fill="url(#frontBlue)"/>
      <path d="M0 0 H214 Q300 190 208 376 H0 Z" fill="var(--green)"/>
      <path role="img" aria-label="Photo of solar panels catching sunlight" d="M0 0 H204 Q288 190 198 376 H0 Z" fill="url(#panelTone)"/>
    </svg>
    <div class="brand">
      <span class="brand__dot"></span>
      <span class="brand__name">VORN UPKEEP</span>
    </div>
    <ul class="services">
      <li>Solar Power System Install</li>
      <li>Services &amp; Maintenance</li>
      <li>Switch Board Upgrade</li>
      <li>Power &amp; Lighting Point</li>
      <li>Wiring, Rewinding &amp; Renovation</li>
    </ul>
  </section>

  <section class="card card--back" aria-label="Card back">
    <svg class="shape" width="620" height="376" viewBox="0 0 620 376">
      <defs>
        <linearGradient id="stripe" x1="0" y1="0" x2="1" y2="0">
          <stop offset="0" stop-color="var(--green-light)"/>
          <stop offset="1" stop-color="var(--green)"/>
        </linearGradient>
      </defs>
      <rect x="0" y="360" width="290" height="16" fill="url(#stripe)"/>
      <path d="M294 328 H620 V376 H266 Q280 336 294 328 Z" fill="var(--blue)"/>
    </svg>
    <div class="brand">
      <span class="brand__dot"></span>
      <span class="brand__name">VORN UPKEEP</span>
    </div>
    <div class="contact">
      <h1 class="contact__name">Alden Ruiz Marsh</h1>
      <p class="contact__role">Managing Director</p>
      <p class="contact__address">48 Harbor Lane, Brookfield,<br>Westvale, US 204518</p>
      <ul class="contact__list">
        <li><svg viewBox="0 0 14 14" aria-hidden="true"><path d="M1 5 Q7 0 13 5 L11 7 L9 5.5 V4.5 H5 V5.5 L3 7 Z M3 8 H11 V12 H3 Z" fill="var(--green)"/></svg>555-014-2290</li>
        <li><svg viewBox="0 0 14 14" aria-hidden="true"><rect x="1" y="3" width="12" height="8" fill="var(--green)"/><path d="M1 3 L7 8 L13 3" stroke="#fff" stroke-width="1.2" fill="none"/></svg>alden@vornupkeep.com</li>
        <li><svg viewBox="0 0 14 14" aria-hidden="true"><circle cx="7" cy="7" r="6" fill="var(--green)"/><path d="M1 7 H13 M7 1 V13 M7 1 Q3 7 7 13 M7 1 Q11 7 7 13" stroke="#fff" stroke-width=".8" fill="none"/></svg>www.vornupkeep.com</li>
      </ul>
    </div>
    <p class="tagline">Solar power system install</p>
  </section>

</main>
</body>
</html>
```